Modern Verdell Tree Care Website

I need a website for a full service Tree Care company. The company provides tree pruning, tree removal, tree preservation, emergency services, stump grinding, and emergency tree services.

Target Market(s)

Customers that need tree services

Industry/Entity Type

Landscaping, Tree Services

Coding

Coded - Design and coding required

Number of Pages Required

5+ page

Font styles to use
Sans Serif

Requirements
Must have
• Good clean design that showcases the services the company provides.
Nice to have
• Services page; contact form, blog, home page, about page

```html
<!DOCTYPE html>
<html lang="en">
<head>
<meta charset="utf-8">
<title>Verdell Tree Care</title>
<link href="https://fonts.googleapis.com/css2?family=Fira+Sans:wght@400;500;600&family=Inter:wght@400;500;600;700&display=swap" rel="stylesheet">
<style>
:root{
  --green:#8cc63f;
  --green-dark:#6fa52a;
  --taupe:#a9a19d;
  --ink:#1f2a1a;
  --text:#3d3d3d;
  --muted:#9a9a9a;
  --orange:#f5a623;
  --footer:#36491f;
  --line:#e6e6e6;
  --white:#ffffff;
}
*{margin:0;padding:0;box-sizing:border-box}
html,body{width:1200px;height:3878px;overflow:hidden;background:var(--white)}
body{position:relative;font-family:"Fira Sans",sans-serif;color:var(--text)}
.abs{position:absolute}

/* Header + hero */
.hero{position:absolute;left:0;top:0;width:1200px;height:708px;
  background:radial-gradient(ellipse at 55% 40%,#5f7a3c 0%,#34502a 40%,#1d2f17 100%);}
.hero-shade{position:absolute;inset:0;background:linear-gradient(180deg,rgba(0,0,0,.25),rgba(0,0,0,.1) 50%,rgba(0,0,0,.3))}
.brand{position:absolute;display:flex;align-items:center;gap:12px;color:var(--white);font-weight:600;letter-spacing:1px}
.brand-square{background:var(--green)}
.brand-header{left:98px;top:20px;font-size:26px}
.brand-header .brand-square{width:44px;height:44px}
.nav{position:absolute;left:592px;top:32px;display:flex;gap:25px;font-size:15px;color:var(--white)}
.nav .active{color:var(--orange)}
.btn-emergency{position:absolute;left:950px;top:24px;width:151px;height:42px;border:1.5px solid var(--orange);border-radius:21px;color:var(--orange);font-size:14px;font-weight:600;display:flex;align-items:center;justify-content:center}
.hero-title{position:absolute;left:0;width:1200px;top:290px;text-align:center;font-size:45px;font-weight:600;color:var(--white)}
.hero-sub{position:absolute;left:0;width:1200px;top:362px;text-align:center;font-size:15px;line-height:26px;color:#eef2ea}
.btn-hero{position:absolute;left:482px;top:465px;width:236px;height:62px;border:2px solid var(--white);border-radius:31px;color:var(--white);font-size:21px;display:flex;align-items:center;justify-content:center}
.hero-arrow{position:absolute;top:358px}

/* About */
.about-photo{position:absolute;left:0;top:708px;width:640px;height:495px;
  background:linear-gradient(180deg,#e4e6e4 0%,#b9c2bd 35%,#4f6a55 70%,#1f3a28 100%);
  clip-path:polygon(0 0,610px 0,590px 40px,575px 70px,560px 110px,570px 150px,548px 185px,565px 230px,578px 290px,600px 340px,612px 400px,625px 440px,638px 495px,0 495px)}
.eyebrow{position:absolute;font-size:16px;color:var(--text)}
.heading{position:absolute;font-size:36px;line-height:42px;font-weight:600;color:var(--taupe)}
.heading .accent{color:var(--green)}
.about-text{position:absolute;left:638px;top:938px;width:465px;font-size:13px;line-height:20px;color:var(--muted)}
.lead{position:absolute;font-size:14px;color:#bdbdbd}

/* Services */
.svc-arrows{position:absolute;left:1040px;top:1376px;display:flex;gap:14px}
.svc-card{position:absolute;top:1432px;width:292px;height:373px}
.svc-photo{width:100%;height:100%}
.svc-label{position:absolute;left:24px;top:342px;width:241px;height:65px;background:#f3f3f3;font-size:19px;font-weight:600;color:var(--ink);display:flex;align-items:center;padding-left:21px;white-space:nowrap;overflow:hidden}

/* Why choose */
.why-photo{position:absolute;left:658px;top:1893px;width:542px;height:554px;
  background:linear-gradient(135deg,#a9cf4a 0%,#6f9a2d 40%,#486d22 65%,#c4de6a 100%);
  clip-path:polygon(240px 20px,320px 0,542px 0,542px 490px,300px 490px,260px 540px,180px 554px,120px 500px,60px 460px,0 420px,10px 300px,40px 200px,110px 120px,170px 60px)}
.features{position:absolute;left:101px;top:2140px;display:grid;grid-template-columns:304px 260px;row-gap:15px;font-size:16.5px;font-weight:500;color:var(--ink)}
.feature{display:flex;align-items:center;gap:10px;height:27px}

/* Testimonials */
.rev-title{position:absolute;left:98px;top:2528px;font-family:"Inter",sans-serif;font-size:20px;font-weight:700;color:#111}
.rev-sub{position:absolute;left:98px;top:2562px;font-family:"Inter",sans-serif;font-size:12px;color:#333}
.rev-card{position:absolute;top:2593px;width:233px;height:185px;background:var(--white);box-shadow:0 8px 18px rgba(0,0,0,.08);font-family:"Inter",sans-serif;padding:22px 18px}
.rev-summary{text-align:center;padding-top:32px}
.rev-summary .label{font-size:14px;font-weight:600;color:#111}
.stars{display:flex;gap:10px;justify-content:center;margin-top:10px}
.rev-summary .based{font-size:10px;margin-top:8px;color:#111}
.rev-summary .based u{font-weight:700}
.rev-summary .source{display:flex;justify-content:center;align-items:center;gap:6px;font-size:13px;font-weight:600;margin-top:8px;color:#111}
.source-dot{width:14px;height:14px;border-radius:50%;background:var(--green)}
.rev-top{display:flex;justify-content:space-between;align-items:center}
.rev-top .when{font-size:9px;color:#666}
.rev-head{font-size:14px;font-weight:600;color:#111;margin-top:14px}
.rev-body{font-size:10px;line-height:17px;color:#666;margin-top:10px}
.rev-name{font-size:10px;font-weight:700;color:#111;margin-top:14px}

/* Contact */
.form-card{position:absolute;left:718px;top:2896px;width:384px;height:496px;border-radius:14px;background:var(--white);box-shadow:0 6px 22px rgba(0,0,0,.1);border:1px solid #f0f0f0}
.f-label{position:absolute;left:26px;font-size:13px;color:#222;font-family:"Inter",sans-serif}
.f-input{position:absolute;left:26px;width:331px;height:41px;border:1px solid var(--line);border-radius:4px;font-size:12px;color:#666;padding:14px 15px;font-family:"Inter",sans-serif}
.f-submit{position:absolute;left:26px;top:419px;width:331px;height:50px;background:var(--green);border-radius:3px;color:var(--white);font-weight:600;font-size:14px;display:flex;align-items:center;justify-content:center;font-family:"Inter",sans-serif}

/* Footer */
.footer{position:absolute;left:0;top:3455px;width:1200px;height:423px;background:var(--footer);color:var(--white);font-family:"Inter",sans-serif}
.brand-footer{left:98px;top:50px;font-size:40px;font-family:"Fira Sans",sans-serif}
.brand-footer .brand-square{width:64px;height:64px}
.f-touch{position:absolute;left:1000px;top:38px;font-size:15px;font-weight:600}
.socials{position:absolute;left:1002px;top:76px;display:flex;gap:10px}
.social{width:25px;height:25px;background:var(--white);border-radius:4px}
.social.round{border-radius:50%}
.f-rule{position:absolute;left:98px;top:163px;width:1003px;height:1px;background:rgba(255,255,255,.25)}
.f-col{position:absolute;top:192px}
.f-col h4{font-size:16px;font-weight:600;margin-bottom:18px}
.f-col li{list-style:none;font-size:12.5px;height:34px}
.f-contact{display:flex;gap:12px;font-size:12.5px;line-height:16px;margin-bottom:14px}
.f-stay h4{font-size:14px;margin-bottom:10px}
.f-stay .small{font-size:9px;margin-bottom:14px}
.f-email{position:absolute;left:0;top:63px;width:251px;height:39px;background:var(--white);border-radius:4px;color:#777;font-size:13px;padding:11px 15px}
.f-subscribe{position:absolute;left:256px;top:63px;width:116px;height:39px;background:var(--green);border-radius:4px;font-size:13px;font-weight:600;display:flex;align-items:center;justify-content:center}
.copyright{position:absolute;right:99px;top:389px;font-size:12px;color:#d9dfd3}
</style>
</head>
<body>

<header class="hero" role="img" aria-label="Photo of a woman tending ferns in a lush green forest">
  <div class="hero-shade"></div>
</header>
<div class="brand brand-header"><span class="brand-square"></span>VERDELL TREE CARE</div>
<nav class="nav">
  <span class="active">Home</span><span>About</span><span>Services</span><span>Blog</span><span>Contact</span>
</nav>
<div class="btn-emergency">Emergency Call</div>
<h1 class="hero-title">Call Verdell for All Your Tree Care Needs</h1>
<p class="hero-sub">Porem ipsum dolor sit amet, consectetur adipiscing elit. Nunc vulputate libero et velit interdum, ac aliquet odio mattis.<br>Class aptent taciti sociosqu ad litora torquent per conubia nostra, per inceptos himenaeos.</p>
<div class="btn-hero">Contact us</div>
<svg class="hero-arrow" style="left:66px" width="22" height="30" viewBox="0 0 22 30"><path d="M16 3 4 15l12 12" fill="none" stroke="#fff" stroke-width="3"/></svg>
<svg class="hero-arrow" style="left:1110px" width="22" height="30" viewBox="0 0 22 30"><path d="M6 3l12 12L6 27" fill="none" stroke="#fff" stroke-width="3"/></svg>

<section>
  <div class="about-photo" role="img" aria-label="Misty evergreen forest under a pale sky"></div>
  <p class="eyebrow" style="left:638px;top:814px">Who we are</p>
  <h2 class="heading" style="left:638px;top:840px">Committed to <span class="accent">Growing</span><br><span class="accent">Greener</span> Communities</h2>
  <p class="about-text">At Verdell Tree Care, we are more than just a tree service company, we are stewards of our beautiful trees. With a passion deeply rooted in arboriculture, we embark on a mission to promote the health, beauty, and safety of your trees and landscapes.<br>Whether it's expert tree trimming to enhance aesthetics, meticulous tree removal to mitigate hazards, or comprehensive tree health assessments to ensure safety, we approach each task with unwavering dedication and attention to detail.</p>
</section>

<section>
  <p class="eyebrow" style="left:98px;top:1259px">Our Services</p>
  <h2 class="heading" style="left:98px;top:1286px"><span class="accent">Quality Services</span> for Every<br><span class="accent">Tree</span> Challenge</h2>
  <p class="lead" style="left:98px;top:1384px">Morem ipsum dolor sit amet, consectetur adipiscing elit.</p>
  <div class="svc-arrows">
  <svg width="22" height="22" viewBox="0 0 22 22"><path d="M20 11H3M10 4l-7 7 7 7" fill="none" stroke="#6fa52a" stroke-width="2"/></svg>
  <svg width="22" height="22" viewBox="0 0 22 22"><path d="M2 11h17M12 4l7 7-7 7" fill="none" stroke="#6fa52a" stroke-width="2"/></svg>
  </div>
  <div class="svc-card" style="left:98px"><div class="svc-photo" role="img" aria-label="Arborist in a bucket lift trimming a leafy tree" style="background:linear-gradient(160deg,#5b8a3a,#2f5a24 55%,#9fb98a)"></div><div class="svc-label">Tree Trimming</div></div>
  <div class="svc-card" style="left:417px"><div class="svc-photo" role="img" aria-label="Arborist cutting a large trunk with a chainsaw" style="background:linear-gradient(160deg,#c9a84a,#7a6a52 45%,#b7b0a0)"></div><div class="svc-label">Tree Removal</div></div>
  <div class="svc-card" style="left:736px"><div class="svc-photo" role="img" aria-label="Forestry machine stacking cut logs" style="background:linear-gradient(170deg,#4f6d36,#8a5a32 55%,#c08a55)"></div><div class="svc-label">Tree Clearing</div></div>
  <div class="svc-card" style="left:1055px"><div class="svc-photo" role="img" aria-label="Gardener pruning branches with shears" style="background:linear-gradient(160deg,#7fa84a,#c7d4b9 60%,#e0e4d8)"></div><div class="svc-label">Tree Pruning</div></div>
</section>

<section>
  <div class="why-photo" role="img" aria-label="Arborist in orange and green workwear inspecting a young tree"></div>
  <p class="eyebrow" style="left:98px;top:1967px">Why Choose Us</p>
  <h2 class="heading" style="left:98px;top:1994px"><span class="accent">Exceptional</span> Care, <span class="accent">Outstanding</span><br>Results</h2>
  <p class="lead" style="left:98px;top:2087px;font-size:16px;color:#a0a0a0">Horem ipsum dolor sit amet, consectetur adipiscing elit.</p>
  <div class="features">
    <div class="feature"><svg width="22" height="14" viewBox="0 0 22 14"><path d="M1 7l4 4 8-9M8 10l2 2 10-10" fill="none" stroke="#f5b91e" stroke-width="2"/></svg>Licensed and Insured</div>
    <div class="feature"><svg width="22" height="14" viewBox="0 0 22 14"><path d="M1 7l4 4 8-9M8 10l2 2 10-10" fill="none" stroke="#f5b91e" stroke-width="2"/></svg>Safety is Our No,1 Priority</div>
    <div class="feature"><svg width="22" height="14" viewBox="0 0 22 14"><path d="M1 7l4 4 8-9M8 10l2 2 10-10" fill="none" stroke="#f5b91e" stroke-width="2"/></svg>24-Hours Emergency Services</div>
    <div class="feature"><svg width="22" height="14" viewBox="0 0 22 14"><path d="M1 7l4 4 8-9M8 10l2 2 10-10" fill="none" stroke="#f5b91e" stroke-width="2"/></svg>Free Estimates</div>
    <div class="feature"><svg width="22" height="14" viewBox="0 0 22 14"><path d="M1 7l4 4 8-9M8 10l2 2 10-10" fill="none" stroke="#f5b91e" stroke-width="2"/></svg>Locally Owned &amp; Operated</div>
    <div class="feature"><svg width="22" height="14" viewBox="0 0 22 14"><path d="M1 7l4 4 8-9M8 10l2 2 10-10" fill="none" stroke="#f5b91e" stroke-width="2"/></svg>Hicensed Arborist on Stal</div>
    <div class="feature"><svg width="22" height="14" viewBox="0 0 22 14"><path d="M1 7l4 4 8-9M8 10l2 2 10-10" fill="none" stroke="#f5b91e" stroke-width="2"/></svg>Professional Work</div>
  </div>
</section>

<section>
  <h3 class="rev-title">What customers say about us</h3>
  <p class="rev-sub">We do our best to provide you the best experience ever</p>
  <svg class="abs" style="left:70px;top:2682px" width="16" height="30" viewBox="0 0 16 30"><path d="M13 2 3 15l10 13" fill="none" stroke="#888" stroke-width="2"/></svg>
  <svg class="abs" style="left:1112px;top:2682px" width="16" height="30" viewBox="0 0 16 30"><path d="M3 2l10 13L3 28" fill="none" stroke="#888" stroke-width="2"/></svg>

  <div class="rev-card rev-summary" style="left:98px">
    <div class="label">Excellent</div>
    <div class="stars">
      <svg width="26" height="26" viewBox="0 0 24 24"><path d="M12 1l3.2 7.2 7.8.7-5.9 5.2 1.8 7.7L12 17.8 5.1 21.8l1.8-7.7L1 8.9l7.8-.7z" fill="#8cc63f"/></svg>
      <svg width="26" height="26" viewBox="0 0 24 24"><path d="M12 1l3.2 7.2 7.8.7-5.9 5.2 1.8 7.7L12 17.8 5.1 21.8l1.8-7.7L1 8.9l7.8-.7z" fill="#8cc63f"/></svg>
      <svg width="26" height="26" viewBox="0 0 24 24"><path d="M12 1l3.2 7.2 7.8.7-5.9 5.2 1.8 7.7L12 17.8 5.1 21.8l1.8-7.7L1 8.9l7.8-.7z" fill="#8cc63f"/></svg>
      <svg width="26" height="26" viewBox="0 0 24 24"><path d="M12 1l3.2 7.2 7.8.7-5.9 5.2 1.8 7.7L12 17.8 5.1 21.8l1.8-7.7L1 8.9l7.8-.7z" fill="#8cc63f"/></svg>
      <svg width="26" height="26" viewBox="0 0 24 24"><path d="M12 1l3.2 7.2 7.8.7-5.9 5.2 1.8 7.7L12 17.8 5.1 21.8l1.8-7.7L1 8.9l7.8-.7z" fill="#8cc63f"/></svg>
    </div>
    <div class="based">Based on <u>456 reviews</u></div>
    <div class="source"><span class="source-dot"></span>ReviewNest</div>
  </div>

  <div class="rev-card" style="left:346px">
    <div class="rev-top"><svg width="94" height="14" viewBox="0 0 94 14"><g fill="#8cc63f"><path id="st" d="M7 0l1.9 4.4 4.6.4-3.5 3 1.1 4.6L7 10 2.9 12.4 4 7.8.5 4.8l4.6-.4z"/><use href="#st" x="19"/><use href="#st" x="38"/><use href="#st" x="57"/><use href="#st" x="76"/></g></svg><span class="when">2 days ago</span></div>
    <div class="rev-head">Best on the market</div>
    <div class="rev-body">I love this product because the support is great. Please ...</div>
    <div class="rev-name">Worldtraveler</div>
  </div>
  <div class="rev-card" style="left:601px">
    <div class="rev-top"><svg width="94" height="14" viewBox="0 0 94 14"><g fill="#8cc63f"><use href="#st"/><use href="#st" x="19"/><use href="#st" x="38"/><use href="#st" x="57"/><use href="#st" x="76"/></g></svg><span class="when">2 days ago</span></div>
    <div class="rev-head">Best on the market</div>
    <div class="rev-body">I love this product because the support is great. Please ...</div>
    <div class="rev-name">Worldtraveler</div>
  </div>
  <div class="rev-card" style="left:854px">
    <div class="rev-top"><svg width="94" height="14" viewBox="0 0 94 14"><g fill="#8cc63f"><use href="#st"/><use href="#st" x="19"/><use href="#st" x="38"/><use href="#st" x="57"/><use href="#st" x="76"/></g></svg><span class="when">2 days ago</span></div>
    <div class="rev-head">Best on the market</div>
    <div class="rev-body">I love this product because the support is great. Please ...</div>
    <div class="rev-name">Worldtraveler</div>
  </div>
</section>

<section>
  <p class="eyebrow" style="left:102px;top:3084px">Contact</p>
  <h2 class="heading" style="left:102px;top:3108px"><span class="accent">Get in Touch</span> with Our Tree<br><span class="accent">Care Specialists</span></h2>
  <p class="lead" style="left:102px;top:3204px">Morem ipsum dolor sit amet, consectetur adipiscing elit.</p>
  <form class="form-card">
    <span class="f-label" style="top:25px">Name</span>
    <div class="f-input" style="top:49px">Your name</div>
    <span class="f-label" style="top:106px">Email</span>
    <div class="f-input" style="top:131px">Email</div>
    <span class="f-label" style="top:189px">Phone</span>
    <div class="f-input" style="top:213px">phone number</div>
    <span class="f-label" style="top:278px">Message</span>
    <div class="f-input" style="top:301px;height:85px">Write message</div>
    <div class="f-submit">Submit</div>
  </form>
</section>

<footer class="footer">
  <div class="brand brand-footer"><span class="brand-square"></span>VERDELL TREE CARE</div>
  <div class="f-touch">Get In Touch</div>
  <div class="socials"><span class="social"></span><span class="social round"></span><span class="social"></span></div>
  <div class="f-rule"></div>
  <div class="f-col" style="left:99px"><h4>Pages</h4><ul><li>Home</li><li>About</li><li>Service</li><li>Blog</li></ul></div>
  <div class="f-col" style="left:242px"><h4>Legal</h4><ul><li>Imprint</li><li>Terms&amp; Condition</li><li>Privacy</li><li>Cookies</li></ul></div>
  <div class="f-col" style="left:385px"><h4>Contact Info</h4>
    <div class="f-contact"><svg width="17" height="12" viewBox="0 0 17 12"><rect x=".5" y=".5" width="16" height="11" fill="none" stroke="#fff"/><path d="M.5 .5l8 6 8-6" fill="none" stroke="#fff"/></svg>hello@verdelltreecare.com</div>
    <div class="f-contact"><svg width="17" height="16" viewBox="0 0 24 24"><path d="M6.6 10.8a15 15 0 0 0 6.6 6.6l2.2-2.2a1 1 0 0 1 1-.25 11 11 0 0 0 3.6.6 1 1 0 0 1 1 1V20a1 1 0 0 1-1 1A17 17 0 0 1 3 4a1 1 0 0 1 1-1h3.5a1 1 0 0 1 1 1c0 1.25.2 2.45.6 3.6a1 1 0 0 1-.25 1z" fill="#fff"/></svg>(555) 014-2739<br>(555) 019-9939</div>
    <div style="font-size:12.5px;margin-left:29px">Call MARLOWE For A Free Estimate</div>
  </div>
  <div class="f-col f-stay" style="left:729px;width:380px;height:120px"><h4>Stay Connected</h4><div class="small">Get In Touch</div>
    <div class="f-email">Enter Your Email</div><div class="f-subscribe">Subscribe</div></div>
  <div class="copyright">© 2024 Verdell All Rights Reserved.</div>
</footer>

</body>
</html>
```